Veltrane Group Business Card Design

The CEO is looking for a new trendy look for his business card.
You can stay with current branding or come up with something new/creative. It can be 3D, including Medical Office buildings. You can use our logo in a variety of colors. Please include name, title, company name, company website, email address, cell number

Target Market(s)

Real Estate Development and Construction

Industry/Entity Type

Health care real estate

Contact Information for Business Card

Rohesh Kamdar, CEO M-604.781.2249 E-roheshkamdar@veltrane.com Address:4180 Lindqvist Ave, Tampa, FL 33482 www.veltrane.com

Font styles to use
Other font styles liked:
• Be creative

Requirements
Must have
• Creative, trendy look
Nice to have
• Please go to our website to get a feel- www. veltrane.com
Should not have
• small fonts

```html
<!DOCTYPE html>
<html lang="en">
<head>
<meta charset="utf-8">
<title>Veltrane Group Business Card</title>
<link href="https://fonts.googleapis.com/css2?family=Poppins:wght@400;600;700;800&display=swap" rel="stylesheet">
<style>
  :root {
    --brand-red: #b21e2b;
    --brand-navy: #1b2b4b;
    --ink: #2a2a2a;
    --paper: #ffffff;
    --backdrop: #9b9b9b;
    --rule: #c9c9c9;
  }
  * { margin: 0; padding: 0; box-sizing: border-box; }
  html, body { width: 1093px; height: 1200px; overflow: hidden; }
  body {
    background: var(--backdrop);
    font-family: "Poppins", sans-serif;
    position: relative;
  }
  .card {
    position: absolute;
    border-radius: 24px;
    overflow: hidden;
  }
  .card--front {
    left: 265px; top: 226px; width: 577px; height: 360px;
    background: var(--paper);
  }
  .card--back {
    left: 265px; top: 621px; width: 582px; height: 357px;
    background: var(--brand-red);
  }
  .wordmark {
    position: absolute;
    font-weight: 800;
    line-height: 0.95;
    text-align: right;
    letter-spacing: -1px;
    white-space: nowrap;
  }
  .card--front .wordmark {
    left: 20px; top: 138px; width: 232px;
    font-size: 46px; color: var(--brand-red);
  }
  .card--back .wordmark {
    left: 0; right: 0; top: 105px;
    text-align: center;
    font-size: 74px; color: var(--paper);
  }
  .divider {
    position: absolute;
    left: 270px; top: 74px; width: 1px; height: 210px;
    background: var(--rule);
  }
  .contact {
    position: absolute;
    left: 290px; top: 92px;
    color: var(--ink);
    white-space: nowrap;
  }
  .contact__name {
    font-size: 23px; font-weight: 700; line-height: 1.1;
    color: var(--brand-red);
  }
  .contact__title {
    font-size: 15.5px; line-height: 1.1; color: var(--brand-navy);
    margin-bottom: 14px;
  }
  .contact__list { list-style: none; }
  .contact__item {
    display: flex; align-items: center; gap: 7px;
    font-size: 15.5px; line-height: 21px;
  }
  .contact__item svg { width: 15px; height: 15px; flex: none; }
  .contact__address {
    margin-top: 15px;
    font-size: 15.5px; line-height: 21px;
  }
  .edge-band {
    position: absolute; left: 0; right: 0; bottom: 0; height: 13px;
  }
</style>
</head>
<body>

<section class="card card--front" aria-label="Business card front">
  <div class="wordmark">Veltrane<br>Group</div>
  <div class="divider"></div>
  <div class="contact">
    <p class="contact__name">Rohesh Kamdar</p>
    <p class="contact__title">CEO</p>
    <ul class="contact__list">
      <li class="contact__item">
        <svg viewBox="0 0 16 16" aria-hidden="true"><path fill="var(--brand-red)" d="M3.5 1.5l2.3 2.8-1.3 1.6c.9 2 2.4 3.6 4.4 4.6l1.6-1.3 2.8 2.3-1.4 2.2C6.5 13.4 2.6 9.5 1.4 3z"/><path fill="none" stroke="var(--brand-red)" stroke-width="1.2" d="M9.5 2.5a4 4 0 0 1 4 4M9.5 0.8a5.8 5.8 0 0 1 5.8 5.8"/></svg>
        604.781.2249
      </li>
      <li class="contact__item">
        <svg viewBox="0 0 16 16" aria-hidden="true"><rect x="0.5" y="3" width="15" height="10" fill="var(--brand-red)"/><path d="M0.5 3.5L8 9l7.5-5.5M0.5 12.5l5.5-4.5M15.5 12.5L10 8" stroke="#fff" stroke-width="1" fill="none"/></svg>
        roheshkamdar@veltrane.com
      </li>
      <li class="contact__item">
        <svg viewBox="0 0 16 16" aria-hidden="true"><g fill="none" stroke="var(--brand-red)" stroke-width="1.3"><circle cx="8" cy="8" r="6.5"/><ellipse cx="8" cy="8" rx="3" ry="6.5"/><path d="M1.5 8h13M2.5 4.8h11M2.5 11.2h11"/></g></svg>
        www.veltrane.com
      </li>
    </ul>
    <p class="contact__address">4180 Lindqvist Ave, Tampa<br>FL 33482</p>
  </div>
  <svg class="edge-band" viewBox="0 0 577 13" preserveAspectRatio="none" aria-hidden="true">
    <rect x="0" y="0" width="577" height="13" fill="var(--brand-red)"/>
    <polygon points="504,0 577,0 577,13 501,13" fill="var(--paper)"/>
    <polygon points="507,0 577,0 577,13 504,13" fill="var(--brand-navy)"/>
  </svg>
</section>

<section class="card card--back" aria-label="Business card back">
  <div class="wordmark">Veltrane<br>Group</div>
</section>

</body>
</html>
```